Business Card Design - Amberfield Court

We are looking at a new design for our business cards that has a modern and professional look. We run a residential aged care facility focussing on the care of residents. The cards will be used for potential clients, consultants and business opportunities in this sector. Blue and white is our main colours and would to see these colours incorporated in the design.
Industry/Entity Type
Business
Contact Information for Business Card
Amberfield Court, Darren Walsh, dwalsh@amberfieldcourt.com.au, Finance Manager, 0472 639 208, BCom, 37 Marrabel Crescent, Brindle Vale, Qld 4093.
Look and feel
Each slider illustrates characteristics of the customer's brand and the style your logo design should communicate.

```html
<!DOCTYPE html>
<html lang="en">
<head>
<meta charset="utf-8">
<title>Amberfield Court – Business Card</title>
<link rel="stylesheet" href="https://fonts.googleapis.com/css2?family=Fira+Sans+Condensed:wght@400;500&display=swap">
<style>
  :root {
    --backdrop: #3b3b3b;
    --brand-blue: #4a7591;
    --brand-navy: #2c4a5e;
    --card-white: #f6f6f6;
    --taupe: #a09389;
    --taupe-line: #b3a69b;
    --ink-light: #ffffff;
  }
  * { margin: 0; padding: 0; box-sizing: border-box; }
  html, body {
    width: 1200px;
    height: 750px;
    overflow: hidden;
    background: var(--backdrop);
    font-family: "Fira Sans Condensed", "Arial Narrow", sans-serif;
  }
  .stage {
    position: relative;
    width: 1200px;
    height: 750px;
  }
  .card {
    position: absolute;
    top: 228px;
    width: 460px;
    height: 262px;
    border-radius: 12px;
    overflow: hidden;
  }
  .card-front {
    left: 124px;
    background: var(--brand-blue);
  }
  .card-back {
    left: 618px;
    background: var(--taupe);
    display: flex;
    flex-direction: column;
    align-items: center;
    justify-content: center;
    gap: 4px;
    padding-bottom: 18px;
  }
  .front-arc {
    position: absolute;
    inset: 0;
    width: 460px;
    height: 262px;
  }
  .holder {
    position: absolute;
    left: 18px;
    top: 16px;
    color: var(--ink-light);
    line-height: 1.15;
  }
  .holder-name {
    font-size: 19px;
    font-weight: 500;
  }
  .holder-credential {
    font-size: 13px;
    font-weight: 500;
  }
  .holder-title {
    font-size: 13px;
    font-weight: 400;
  }
  .brand-name {
    position: absolute;
    left: 0;
    right: 0;
    top: 170px;
    text-align: center;
    font-size: 25px;
    font-weight: 400;
    letter-spacing: 2px;
    color: var(--brand-navy);
  }
  .contact-line {
    color: var(--ink-light);
    font-size: 14px;
    font-weight: 400;
    line-height: 1.3;
  }
</style>
</head>
<body>
<main class="stage">
  <section class="card card-front">
    <svg class="front-arc" viewBox="0 0 460 262" aria-hidden="true">
      <path d="M1,262 C1,92 98,34 232,34 C366,34 460,92 460,262 Z" fill="var(--taupe-line)"/>
      <path d="M3,262 C3,96 100,38 232,38 C364,38 460,96 460,262 Z" fill="var(--card-white)"/>
    </svg>
    <div class="holder">
      <div class="holder-name">Darren Walsh <span class="holder-credential">BCom</span></div>
      <div class="holder-title">Finance Manager</div>
    </div>
    <div class="brand-name">AMBERFIELD COURT</div>
  </section>

  <section class="card card-back">
    <p class="contact-line">37 Marrabel Crescent, Brindle Vale, Qld 4093.</p>
    <p class="contact-line">0472 639 208 | dwalsh@amberfieldcourt.com.au</p>
    <p class="contact-line">www.amberfieldcourt.com.au</p>
  </section>
</main>
</body>
</html>
```